A website where experts collaborate on your project

I am building a new website where experts (yes, like designers) collaborate on projects with the project owner. More minds = more collaboration = better end product. Please see Pelmora(dot)com for a quick landing page I created for collaborating on presentations (although there will be many project types offered)

I am looking for a DESIGNER LONG TERM, but for now, just need initial mock ups to show the web programmers.

I have 21 Word documents loosely designed, what I would like to see here is a theme. Please DO NOT GO OFF WHAT YOU CURRENTLY SEE AT PELMORA. What is up now is only a quick landing page.

You can view a Word doc of the homepage here:
https://www.filevanta.com/s/qx83kdm2/home.docx?dl=0

WHAT AM I LOOKING FOR?
A clean, well designed theme.

Here is a link to the logo:
https://www.filevanta.com/s/mr47tpz9/logo%20-%20horizontal.tif?dl=0
-----------------------------------------
Here are a few sites I like the design of and what I like about them:
www.quenbrook.com-all around my favorite, beautiful graphics, clean layout, bold use of colors on a dark background
Ravelto.com- clean layout, The use of humans and bubble style elements.
Mintharbor.com :) clean, bold, unique pop art style but professional
plumevault.com - From the unique colors and artwork and the ability of that art to not interfere with the important elements of the site
sparkwidgets.com-clean, nice colors, well organized and separated sections.
www.dunmereco.com-love the font, use of colors and sectionalized style

All in all, I am not picky and open to so many styles. I would ultimately like the designer I pick to design all 21 pages.
Updates

Hello everyone,Moving forward, I would like you all to pay special attention to the section in my brief titled "Here are a few sites I like the design of and what I like about them". Please see below, I handpicked each one of these as sites I really like. Thank you.Here are a few sites I like the design of and what I like about them:Ravelto.com- clean layout, The use of humans and bubble style elements.Mintharbor.com :) clean, bold, unique pop art style but professionalwriteraccess.com - From the unique colors and artwork and the ability of that art to not interfere with the important elements of the sitegrowthgeeks.com-clean, nice colors, well organized and separated sections.www.dunmereco.com-love the font, use of colors and sectionalized stylewww.quenbrook.com-beautiful graphics, clean layout, bold use of colors----------------------------------------- Added Tuesday, November 24, 2015

I updated the homepage, you can see it here:https://www.dropbox.com/s/kwlkbsookq3cg2m/1new%20homepage.docx?dl=0I am modeling it after my favorite designed site: triplelift.comI love the dark colors with the orange glowing style boldness of the buttons. It's real clean too. Added Tuesday, November 24, 2015

Target Market(s)

small business owners, marketers, freelancer writers, graphic designers,

Industry/Entity Type

Building

Number of Pages Required

5+ page

Requirements
Must have
• I can't think of anything the project must have.
Nice to have
• WHAT AM I LOOKING FOR?
• A clean, well designed theme. I had a designer do a bit of work putting elements together, I found it to be very plain, but I like the Application Page (https://www.filevanta.com/s/jb19ckr3/Pelmora-Website.ai?dl=0)
• Here is a link to the logo:
• https://www.filevanta.com/s/mr47tpz9/logo%20-%20horizontal.tif?dl=0
• Here are a few sites I like the design of and what I like about them:
• Ravelto.com- clean layout, The use of humans and bubble style elements.
• Mintharbor.com :) clean, bold, unique pop art style but professional
• plumevault.com - From the unique colors and artwork and the ability of that art to not interfere with the important elements of the site
• sparkwidgets.com-clean, nice colors, well organized and separated sections.
• www.dunmereco.com-love the font, use of colors and sectionalized style
• www.quenbrook.com-beautiful graphics, clean layout, bold use of colors
• -----------------------------------------
Should not have
• out of the boxed, templated style website. I want this site to be memorable and not look like a thousand others

```html
<!DOCTYPE html>
<html lang="en">
<head>
<meta charset="utf-8">
<title>Pelmora — Home</title>
<link href="https://fonts.googleapis.com/css2?family=Open+Sans:wght@400;600;700&family=Raleway:wght@800&display=swap" rel="stylesheet">
<style>
:root{
  --orange:#f7941e;
  --orange-dark:#e5801a;
  --blue:#2aa3d6;
  --teal:#5bb8d6;
  --ink:#333333;
  --muted:#777777;
  --line:#dddddd;
  --gray-bg:#efefef;
  --topbar:#f1f1f1;
  --white:#ffffff;
}
*{margin:0;padding:0;box-sizing:border-box}
html,body{width:718px;height:1200px;overflow:hidden}
body{position:relative;font-family:"Open Sans",Arial,sans-serif;color:var(--ink);background:var(--white)}
.abs{position:absolute}

/* top bar */
.topbar{left:0;top:0;width:718px;height:32px;background:var(--topbar)}
.search{left:59px;top:8px;width:95px;height:44px;border:1px solid #f4c98e;background:var(--white)}
.search-head{height:17px;background:var(--orange);color:var(--white);font-size:7px;padding:4px 6px;text-transform:uppercase;position:relative}
.search-head svg{position:absolute;right:6px;top:6px}
.search-item{font-size:6px;color:var(--muted);padding:2px 5px;border-bottom:1px solid #f1e2cc;height:12px}
.chat{top:10px}

/* header */
.brand{left:60px;top:66px;font-size:22px;font-weight:600;color:var(--ink);letter-spacing:.5px}
.nav{top:70px;left:0;width:718px;height:22px}
.nav a{position:absolute;top:0;height:22px;line-height:22px;font-size:6.5px;font-weight:600;color:var(--orange);text-decoration:none;text-transform:uppercase}
.nav a.active{border:1px solid var(--teal);border-radius:2px;padding:0 9px;line-height:20px}

/* hero */
.hero{left:0;top:129px;width:718px;height:311px;background:linear-gradient(100deg,#7a5a44 0%,#b9a99a 30%,#8696a6 55%,#c9d6e0 80%,#e6edf2 100%)}
.hero-panel{left:355px;top:236px;width:304px;height:137px;background:rgba(110,115,122,.45)}
.hero-title{right:79px;top:253px;font-family:"Raleway",Arial,sans-serif;font-weight:800;font-size:19px;color:var(--white);letter-spacing:.2px}
.hero-sub{right:77px;top:286px;width:200px;text-align:right;font-size:7.8px;line-height:13px;color:var(--white)}
.btn{background:var(--orange);color:var(--white);font-weight:700;font-size:7.5px;text-transform:uppercase;text-align:center;border-radius:2px}
.hero-btn{left:571px;top:327px;width:72px;height:28px;line-height:28px}
.hero-next{left:680px;top:260px}

/* listing section */
.listing{left:0;top:440px;width:718px;height:457px;background:var(--gray-bg)}
.filter{left:79px;top:479px;width:172px;height:377px;background:var(--white);border:1px solid #d6d6d6}
.filter-title{position:absolute;left:12px;top:12px;font-size:7.5px;font-weight:700;color:var(--orange);text-transform:uppercase}
.filter-rule{position:absolute;left:12px;right:0;top:28px;border-top:1px dashed #cfcfcf}
.filter-price{position:absolute;left:15px;top:44px;font-size:6.5px;display:flex;align-items:center;gap:8px}
.toggle{width:9px;height:9px;border-radius:1px;background:var(--orange);position:relative;flex:none}
.toggle::before{content:"";position:absolute;left:2px;right:2px;top:4px;height:1px;background:var(--white)}
.toggle.plus::after{content:"";position:absolute;top:2px;bottom:2px;left:4px;width:1px;background:var(--white)}
.slider{position:absolute;left:32px;top:72px}
.range{position:absolute;top:90px;left:18px;font-size:7px;display:flex;align-items:center}
.range .box{width:45px;height:17px;border:1px solid #cfcfcf;border-radius:2px;font-size:6px;padding:4px 5px;margin-left:4px}
.filter-list{position:absolute;left:0;right:0;top:119px;list-style:none}
.filter-list li{height:30.7px;border-top:1px solid #e4e4e4;display:flex;align-items:center;gap:8px;padding-left:15px;font-size:6px;text-transform:uppercase}
.save-btn{position:absolute;left:56px;top:344px;width:60px;height:23px;line-height:23px;font-size:6.5px}

.projects{left:287px;top:479px;width:351px;height:377px;background:var(--white);border:1px solid #f0d6b3}
.proj-head{position:absolute;left:0;top:0;width:100%;height:26px;background:var(--orange);color:var(--white);font-size:6px;font-weight:600;text-transform:uppercase}
.proj-head span{position:absolute;top:9px}
.proj-head .main{font-size:7.5px;font-weight:700;top:8px;left:9px}
.proj-head i{position:absolute;top:8px;width:1px;height:10px;background:rgba(255,255,255,.8)}
.row{position:absolute;left:0;width:100%;border-top:1px solid #e6e6e6}
.row .desc{position:absolute;left:11px;width:125px;font-size:7.8px;line-height:13.4px;color:#444}
.row .price,.row .country{position:absolute;font-size:7px;font-weight:700;color:#333;text-align:center}
.col{position:absolute;top:26px;bottom:0;width:1px;background:#e6e6e6}
.days-tag{position:absolute;width:45px;height:17px;line-height:17px;background:var(--teal);color:var(--white);font-size:6px;font-weight:600;text-align:center;text-transform:uppercase}

/* testimonials */
.t-title{left:0;top:932px;width:718px;text-align:center;font-size:14px;font-weight:700;color:var(--orange)}
.t-arrows{left:341px;top:963px}
.t-quote{left:115px;top:994px;width:340px;text-align:right;font-size:6.5px;line-height:13.4px;color:#333}
.t-price{left:330px;top:1056px;font-size:8px;color:#555}
.t-price b{color:var(--orange)}
.t-stars{left:394px;top:1057px}
.t-name{left:300px;top:1074px;width:155px;text-align:right;font-size:7.5px;font-weight:700;color:var(--orange)}
.t-photo{left:472px;top:990px}

/* footer */
.footer{left:0;top:1118px;width:718px;height:82px;background:var(--orange)}
.social{left:240px;top:1133px}
.copyright{left:0;top:1174px;width:718px;text-align:center;font-size:7.5px;color:var(--white)}
</style>
</head>
<body>

<div class="abs topbar"></div>
<div class="abs search">
  <div class="search-head">Search
    <svg width="7" height="4" viewBox="0 0 7 4"><path d="M0 0h7L3.5 4z" fill="#fff"/></svg>
  </div>
  <div class="search-item">- Free Lancers</div>
  <div class="search-item">- Projects</div>
</div>
<svg class="abs chat" style="left:590px" width="70" height="14" viewBox="0 0 70 14" aria-hidden="true">
  <ellipse cx="9" cy="6" rx="7" ry="5" fill="#f7941e"/><path d="M5 10l-2 3 5-2z" fill="#f7941e"/>
  <text x="9" y="8" font-size="5" fill="#fff" text-anchor="middle" font-family="Open Sans, sans-serif">10</text>
  <ellipse cx="35" cy="6" rx="7" ry="5" fill="#cfcfcf"/><path d="M31 10l-2 3 5-2z" fill="#cfcfcf"/>
  <ellipse cx="61" cy="6" rx="7" ry="5" fill="#cfcfcf"/><path d="M57 10l-2 3 5-2z" fill="#cfcfcf"/>
</svg>

<div class="abs brand">Pelmora</div>

<nav class="abs nav">
  <a class="active" href="#" style="left:368px">Home</a>
  <a href="#" style="left:428px">Projects</a>
  <a href="#" style="left:489px">How it works</a>
  <a href="#" style="left:569px">Plan</a>
  <a href="#" style="left:616px">My Account</a>
</nav>

<div class="abs hero" role="img" aria-label="Photo of two business colleagues working together at a laptop in a bright office"></div>
<div class="abs hero-panel"></div>
<div class="abs hero-title">CONVERT MORE CUSTOMERS</div>
<div class="abs hero-sub">Experience the power of experts collaborating on your project.</div>
<div class="abs btn hero-btn">Get Started</div>
<svg class="abs hero-next" width="16" height="48" viewBox="0 0 16 48" aria-hidden="true"><path d="M1 1l14 23L1 47" fill="none" stroke="rgba(255,255,255,.7)" stroke-width="1"/></svg>

<div class="abs listing"></div>

<aside class="abs filter">
  <div class="filter-title">Fliter by</div>
  <div class="filter-rule"></div>
  <div class="filter-price"><span class="toggle"></span>Price</div>
  <svg class="slider" width="122" height="12" viewBox="0 0 122 12" aria-hidden="true">
    <line x1="6" y1="6" x2="116" y2="6" stroke="#f7941e" stroke-width="1.5"/>
    <circle cx="6" cy="6" r="5.5" fill="#f7941e"/><circle cx="116" cy="6" r="5.5" fill="#f7941e"/>
  </svg>
  <div class="range">$<span class="box">20</span><span style="margin-left:28px">to $</span><span class="box">1000 +</span></div>
  <ul class="filter-list">
    <li><span class="toggle plus"></span>Country</li>
    <li><span class="toggle plus"></span>Categories</li>
    <li><span class="toggle plus"></span>Time left</li>
    <li><span class="toggle plus"></span>Active | Expired</li>
    <li><span class="toggle plus"></span>Contains adult content</li>
    <li><span class="toggle plus"></span>Keywords</li>
    <li><span class="toggle plus"></span>Followers</li>
  </ul>
  <div class="btn save-btn">Save Filter</div>
</aside>

<section class="abs projects">
  <div class="proj-head">
    <span class="main">Crowd Projects</span>
    <i style="left:145px"></i><span style="left:162px">Sort: Price</span>
    <i style="left:213px"></i><span style="left:232px">Country</span>
    <i style="left:282px"></i><span style="left:300px">Time left</span>
  </div>
  <div class="col" style="left:145px"></div>
  <div class="col" style="left:213px"></div>
  <div class="col" style="left:282px"></div>

  <div class="row" style="top:26px;height:85px;border-top:none">
    <div class="desc" style="top:28px">Lorem Ipsum is simply dummy text of the printing and typeset-ting industry.</div>
    <div class="price" style="left:145px;width:68px;top:46px">$ 80K</div>
    <div class="country" style="left:213px;width:69px;top:48px">UK</div>
    <div class="days-tag" style="left:294px;top:43px">6 Days</div>
  </div>
  <div class="row" style="top:111px;height:88px">
    <div class="desc" style="top:26px">Lorem Ipsum is simply dummy text of the printing and typeset-ting industry.</div>
    <div class="price" style="left:145px;width:68px;top:44px">$ 250K</div>
    <div class="country" style="left:213px;width:69px;top:46px">US</div>
    <div class="days-tag" style="left:294px;top:41px">6 Days</div>
  </div>
  <div class="row" style="top:199px;height:88px">
    <div class="desc" style="top:28px">Lorem Ipsum is simply dummy text of the printing and typeset-ting industry.</div>
    <div class="price" style="left:145px;width:68px;top:46px">$62,</div>
    <div class="country" style="left:213px;width:69px;top:48px">UK</div>
    <div class="days-tag" style="left:294px;top:43px">6 Days</div>
  </div>
  <div class="row" style="top:287px;height:88px">
    <div class="desc" style="top:28px">Lorem Ipsum is simply dummy text of the printing and typeset-ting industry.</div>
    <div class="price" style="left:145px;width:68px;top:46px">$48,</div>
    <div class="country" style="left:213px;width:69px;top:48px">US</div>
    <div class="days-tag" style="left:294px;top:43px">6 Days</div>
  </div>
</section>

<h2 class="abs t-title">Our Testimonials</h2>
<svg class="abs t-arrows" width="36" height="14" viewBox="0 0 36 14" aria-hidden="true">
  <circle cx="7" cy="7" r="7" fill="#d9d9d9"/><path d="M8.5 4L6 7l2.5 3" stroke="#fff" stroke-width="1.4" fill="none"/>
  <circle cx="28" cy="7" r="7" fill="#d9d9d9"/><path d="M26.5 4L29 7l-2.5 3" stroke="#fff" stroke-width="1.4" fill="none"/>
</svg>
<p class="abs t-quote">“With Pelmora I have multiple experts perfecting my content and I only pay for the feedback I find valuable. It’s perfect””With Pelmora I have multipleexperts perfecting my content and I only pay for the feedback I find valuable. It’s perfect””With Pelmora I have multiple experts perfecting my content and I only pay for the feedback I find valuable. It’s perfect””</p>
<div class="abs t-price"><b>$62</b> monthly</div>
<svg class="abs t-stars" width="62" height="8" viewBox="0 0 64 10" aria-label="4.5 star rating">
  <g fill="#f2c230">
    <path d="M5 0l1.5 3.2 3.5.4-2.6 2.4.7 3.5L5 7.8 1.9 9.5l.7-3.5L0 3.6l3.5-.4z"/>
    <path transform="translate(13 0)" d="M5 0l1.5 3.2 3.5.4-2.6 2.4.7 3.5L5 7.8 1.9 9.5l.7-3.5L0 3.6l3.5-.4z"/>
    <path transform="translate(26 0)" d="M5 0l1.5 3.2 3.5.4-2.6 2.4.7 3.5L5 7.8 1.9 9.5l.7-3.5L0 3.6l3.5-.4z"/>
    <path transform="translate(39 0)" d="M5 0l1.5 3.2 3.5.4-2.6 2.4.7 3.5L5 7.8 1.9 9.5l.7-3.5L0 3.6l3.5-.4z"/>
  </g>
  <path transform="translate(52 0)" d="M5 0l1.5 3.2 3.5.4-2.6 2.4.7 3.5L5 7.8 1.9 9.5l.7-3.5L0 3.6l3.5-.4z" fill="none" stroke="#f2c230" stroke-width=".8"/>
  <path transform="translate(52 0)" d="M5 0v7.8L1.9 9.5l.7-3.5L0 3.6l3.5-.4z" fill="#f2c230"/>
</svg>
<div class="abs t-name">Dean Holloway, CEO, Brickline 52</div>
<svg class="abs t-photo" width="122" height="96" viewBox="0 0 122 96" role="img" aria-label="Portrait photo of a smiling businessman in a suit">
  <defs><linearGradient id="portrait" x1="0" y1="0" x2="1" y2="1"><stop offset="0" stop-color="#eef1f4"/><stop offset=".6" stop-color="#9aa4ae"/><stop offset="1" stop-color="#2e3640"/></linearGradient></defs>
  <path d="M67 2c28 0 52 19 52 45s-22 46-50 46c-9 0-18-2-25-6L1 93l32-10C24 75 17 62 17 47 17 21 39 2 67 2z" fill="url(#portrait)" stroke="#999" stroke-width=".8"/>
</svg>

<footer class="abs footer"></footer>
<svg class="abs social" width="240" height="28" viewBox="0 0 240 28" aria-label="Social links">
  <g fill="none" stroke="#fff" stroke-width="1.6">
    <circle cx="13" cy="14" r="12"/><circle cx="55" cy="14" r="12"/><circle cx="98" cy="14" r="12"/>
    <circle cx="140" cy="14" r="12"/><circle cx="182" cy="14" r="12"/><circle cx="224" cy="14" r="12"/>
  </g>
</svg>
<p class="abs copyright">© 2015 Pelmora. All Rights Reserved</p>

</body>
</html>
```